Distribution/Printing company needs a web site to inform prospective customers on what we do.

Distribution/Printing/Packaging company needs a web site to inform prospective customers on what we do. Please look at our direct to consumer web site (under development) for an idea of the product lines we sell: storedev.maplewickhaven.com
Logo files are attached as is a flyer that is under development which contains other information about the company (this is to be used for content- not to be posted as is). The web site should be focused on our business customer base and is not intended to be direct to consumer. Site should have a link to our consumer web site.
Site design should be mobile friendly, or mobile could be redirected to a mobile version. This web site will be strictly informational and will not be designed for any sales transactions.

Target Market(s)

Manufacturing and retail businesses, any other multi-site business that would benefit from centralized pricing and budget controls we can provide (banks, medical/dental offices, educational facilities, etc).

Industry/Entity Type

It Company

Coding

Coded - Design and coding required

Number of Pages Required

5+ page

Requirements
Must have
• 1) Top level menu: Products, about us, locations, contact us, news
• 2) page with news/promotions that is easily updated
• 3) "contact us" form (name, company, phone, email address) email link
• 4) link to www.store.maplewickhaven.com with information that lower pricing is available for businesses
• 5) SEO keywords
• 6) Link to powerpoint presentation file
Nice to have
• 1) our phone number should appear on every page near the top

```html
<!DOCTYPE html>
<html lang="en">
<head>
<meta charset="utf-8">
<title>Maplewick Haven Supply — Packaging, Printing, Distribution</title>
<link rel="stylesheet" href="https://fonts.googleapis.com/css2?family=Open+Sans:wght@400;600;700&family=Roboto+Slab:wght@100;300;400;700;900&display=swap">
<style>
:root{
  --red:#9b0a0c;
  --red-bright:#e0161c;
  --ink:#222;
  --muted:#666;
  --band:#ececec;
  --card-line:#dcdcdc;
  --footer:#242424;
  --footer-deep:#161616;
  --footer-text:#8c8c8c;
  --white:#fff;
  --slab:"Roboto Slab", serif;
  --sans:"Open Sans", sans-serif;
}
*{box-sizing:border-box;margin:0;padding:0}
html,body{width:1200px;height:2323px;overflow:hidden;background:var(--white)}
body{position:relative;font-family:var(--slab);color:var(--ink)}
a{color:inherit;text-decoration:none}

/* header */
.site-header{position:absolute;left:0;top:0;width:1200px;height:124px;background:var(--white)}
.brand{position:absolute;left:99px;top:40px;display:flex;align-items:center;gap:12px}
.brand-mark{width:26px;height:26px;background:var(--ink)}
.brand-name{font-family:var(--sans);font-weight:700;font-size:21px;letter-spacing:.5px;color:var(--ink)}
.brand-tag{position:absolute;left:99px;top:84px;font-family:var(--sans);font-weight:700;font-size:12.5px;color:var(--ink)}
.main-nav{position:absolute;left:576px;top:0;height:88px;display:flex;font-family:var(--sans);font-size:12px;font-weight:600}
.main-nav a{display:block;height:88px;line-height:132px;color:#333;padding:0 17px}
.main-nav a.is-active{background:#111;color:var(--white);padding:0 23px;border-bottom:5px solid var(--red-bright);line-height:127px;height:88px}
.search-icon{position:absolute;left:1072px;top:53px}

/* hero */
.hero{position:absolute;left:0;top:124px;width:1200px;height:506px;background:linear-gradient(90deg,#3a3a3a 0%,#6a6a6a 45%,#505050 100%)}
.hero-photo{position:absolute;left:553px;top:105px;width:538px;height:347px;background:linear-gradient(160deg,#d9ab72,#b0783f);border-radius:4px}
.hero-copy{position:absolute;left:133px;top:128px;color:var(--white)}
.hero-copy .lead{font-weight:100;font-size:54px;line-height:1}
.hero-copy .accent{font-weight:900;font-size:52px;color:var(--red-bright);line-height:1;margin-top:16px;letter-spacing:1px}
.hero-copy .title{font-weight:300;font-size:54px;line-height:1;margin-top:16px}
.hero-arrow{position:absolute;top:232px}
.hero-arrow.prev{left:31px}
.hero-arrow.next{left:1128px}

/* services */
.services-band{position:absolute;left:0;top:630px;width:1200px;height:302px;background:var(--band)}
.service-card{position:absolute;top:580px;width:288px;height:318px;background:var(--white);border:1px solid #d6d6d6;box-shadow:0 14px 10px -8px rgba(0,0,0,.35);text-align:center}
.service-card h2{height:46px;line-height:48px;font-weight:400;font-size:20px;color:#222}
.service-photo{height:139px}
.service-card p{font-weight:300;font-size:12px;line-height:20px;color:#444;padding:18px 40px 0}
.read-more{display:block;margin-top:14px;font-weight:700;font-size:12px;color:var(--red)}

/* products */
.section-title{position:absolute;left:101px;top:978px;font-weight:400;font-size:27px;color:#222}
.product-card{position:absolute;width:231px;height:309px;background:#f0f0f0;border:1px solid #e0e0e0;text-align:center}
.product-photo{margin:8px;height:144px;background:var(--white);border:1px solid #e6e6e6;position:relative}
.product-photo span{position:absolute;inset:22px 40px;border-radius:6px}
.product-card h3{margin-top:16px;font-weight:700;font-size:19px;color:var(--red)}
.product-card p{font-weight:300;font-size:12px;line-height:20px;color:#555;padding:6px 18px 0}
.btn{display:inline-block;margin-top:16px;width:102px;height:32px;line-height:32px;background:var(--red);color:var(--white);font-size:12px}

/* benefits */
.benefits{position:absolute;left:99px;top:1791px;width:1002px;height:149px;background:#000;overflow:hidden}
.benefits .mid{position:absolute;left:320px;top:0;width:400px;height:149px;background:var(--red);transform:skewX(-12deg)}
.benefit{position:absolute;top:18px;color:var(--white)}
.benefit h4{font-weight:700;font-size:19px}
.benefit p{font-weight:300;font-size:12.5px;line-height:20px;color:#ddd;width:180px;margin-top:12px}
.benefit svg{position:absolute;top:8px}

/* footer */
.site-footer{position:absolute;left:0;top:1992px;width:1200px;height:233px;background:var(--footer)}
.footer-col{position:absolute;top:28px;color:var(--footer-text);font-weight:300;font-size:12px;line-height:20px}
.footer-col h5{font-family:var(--sans);font-weight:400;font-size:17px;color:#e6e6e6;margin-bottom:10px}
.footer-col ul{list-style:none}
.footer-col li::before{content:"›";color:var(--red-bright);font-weight:700;margin-right:8px}
.footer-col .hot{color:var(--red-bright)}
.footer-bottom{position:absolute;left:0;top:2225px;width:1200px;height:98px;background:var(--footer-deep);color:var(--footer-text);font-size:12px}
.copyright{position:absolute;left:101px;top:25px}
.social{position:absolute;left:101px;top:52px;display:flex;gap:9px}
.social span{width:13px;height:13px;border-radius:50%;background:#9a9a9a}
.help{position:absolute;left:899px;top:12px}
.help b{color:#a6d23a;font-weight:400;font-size:15px}
.footer-links{position:absolute;right:99px;top:50px;display:flex;gap:6px}
.footer-links a+a{border-left:1px solid #555;padding-left:6px}
</style>
</head>
<body>

<header class="site-header">
  <div class="brand"><span class="brand-mark"></span><span class="brand-name">MAPLEWICK HAVEN SUPPLY</span></div>
  <div class="brand-tag">Packaging • Printing • Distribution</div>
  <nav class="main-nav">
    <a class="is-active" href="#">Home</a><a href="#">Services</a><a href="#">New</a><a href="#">Blog</a><a href="#">Portfolio</a><a href="#">Contact us</a>
  </nav>
  <svg class="search-icon" width="22" height="22" viewBox="0 0 22 22"><circle cx="9" cy="9" r="6.5" fill="none" stroke="#333" stroke-width="3"/><line x1="14" y1="14" x2="20" y2="20" stroke="#333" stroke-width="3.5" stroke-linecap="round"/></svg>
</header>

<section class="hero">
  <div class="hero-photo" role="img" aria-label="Stack of cardboard shipping boxes in a warehouse"></div>
  <div class="hero-copy">
    <div class="lead">Providing</div>
    <div class="accent">HIGH QUALITY</div>
    <div class="title">Packing Solutions</div>
  </div>
  <svg class="hero-arrow prev" width="40" height="40" viewBox="0 0 40 40"><circle cx="20" cy="20" r="17" fill="none" stroke="#fff" stroke-width="3"/><path d="M23 11 13 20l10 9z" fill="#fff"/></svg>
  <svg class="hero-arrow next" width="40" height="40" viewBox="0 0 40 40"><circle cx="20" cy="20" r="17" fill="none" stroke="#fff" stroke-width="3"/><path d="M17 11l10 9-10 9z" fill="#fff"/></svg>
</section>

<div class="services-band"></div>
<article class="service-card" style="left:99px">
  <h2>DISTRIBUTION</h2>
  <div class="service-photo" role="img" aria-label="Courier carrying a parcel beside a delivery van" style="background:linear-gradient(90deg,#d8b420,#3a6fb0 60%,#8a8a8a)"></div>
  <p>Lorem Ipsum is simply dummy text of the printing and typesetting industry.</p>
  <a class="read-more" href="#">READ MORE »</a>
</article>
<article class="service-card" style="left:455px">
  <h2>PRINTING</h2>
  <div class="service-photo" role="img" aria-label="Printer checking colour proofs" style="background:linear-gradient(90deg,#d03a5a,#e6b030 45%,#2c3560)"></div>
  <p>Lorem Ipsum is simply dummy text of the printing and typesetting industry.</p>
  <a class="read-more" href="#">READ MORE »</a>
</article>
<article class="service-card" style="left:813px">
  <h2>PACKAGING</h2>
  <div class="service-photo" role="img" aria-label="Worker taping a cardboard box" style="background:linear-gradient(90deg,#c59a6a,#2a3a7a 50%,#d2b08a)"></div>
  <p>Lorem Ipsum is simply dummy text of the printing and typesetting industry.</p>
  <a class="read-more" href="#">READ MORE »</a>
</article>

<h2 class="section-title">Featured Product</h2>

<article class="product-card" style="left:99px;top:1062px"><div class="product-photo" role="img" aria-label="Microwave oven"><span style="background:linear-gradient(#e4e4e4,#a8a8a8)"></span></div><h3>Microwave</h3><p>Lorem Ipsum is simply dummy text of the printing.</p><a class="btn" href="#">Read More</a></article>
<article class="product-card" style="left:356px;top:1062px"><div class="product-photo" role="img" aria-label="Two-wheel hand truck with boxes"><span style="background:linear-gradient(#f2e6d6,#d3a775)"></span></div><h3>Hand Truck 2-Wheel</h3><p>Lorem Ipsum is simply dummy text of the printing.</p><a class="btn" href="#">Read More</a></article>
<article class="product-card" style="left:613px;top:1062px"><div class="product-photo" role="img" aria-label="Tape dispenser sealing a box"><span style="background:linear-gradient(#d64040,#c8935e)"></span></div><h3>Dispenser Tape</h3><p>Lorem Ipsum is simply dummy text of the printing.</p><a class="btn" href="#">Read More</a></article>
<article class="product-card" style="left:869px;top:1062px"><div class="product-photo" role="img" aria-label="Rolls of coloured desktop tape"><span style="background:linear-gradient(90deg,#e05aa0,#48b0e0,#9bd040,#f0a030)"></span></div><h3>Desktop Tape</h3><p>Lorem Ipsum is simply dummy text of the printing.</p><a class="btn" href="#">Read More</a></article>

<article class="product-card" style="left:99px;top:1421px"><div class="product-photo" role="img" aria-label="Microwave oven"><span style="background:linear-gradient(#e4e4e4,#a8a8a8)"></span></div><h3>Microwave</h3><p>Lorem Ipsum is simply dummy text of the printing.</p><a class="btn" href="#">Read More</a></article>
<article class="product-card" style="left:356px;top:1421px"><div class="product-photo" role="img" aria-label="Green and orange sponge scrub"><span style="background:linear-gradient(#3f8a3a 45%,#f08a20 45%)"></span></div><h3>Sponge Scrub</h3><p>Lorem Ipsum is simply dummy text of the printing.</p><a class="btn" href="#">Read More</a></article>
<article class="product-card" style="left:613px;top:1421px"><div class="product-photo" role="img" aria-label="Canister carpet sweeper"><span style="background:linear-gradient(#c8202a,#3a3a3a)"></span></div><h3>Carpet Sweeper</h3><p>Lorem Ipsum is simply dummy text of the printing.</p><a class="btn" href="#">Read More</a></article>
<article class="product-card" style="left:869px;top:1421px"><div class="product-photo" role="img" aria-label="Roll of bubble wrap with dispenser"><span style="background:linear-gradient(#f4f4f4,#bcbcbc)"></span></div><h3>Bubble Wrap</h3><p>Lorem Ipsum is simply dummy text of the printing.</p><a class="btn" href="#">Read More</a></article>

<section class="benefits">
  <div class="mid"></div>
  <div class="benefit" style="left:18px"><h4>Profit Effiency</h4><p>Lorem Ipsum is simply dummy text of the printing and type-setting industry.</p>
    <svg style="left:190px" width="90" height="100" viewBox="0 0 90 100"><path d="M35 20h20l-6 10c20 8 30 28 30 45 0 14-14 20-34 20S11 89 11 75c0-17 10-37 30-45z" fill="#fff"/><text x="45" y="82" text-anchor="middle" font-family="Roboto Slab, serif" font-weight="700" font-size="34" fill="#000">$</text></svg></div>
  <div class="benefit" style="left:362px"><h4>Order Scheduling</h4><p>Lorem Ipsum is simply dummy text of the printing and type-setting industry.</p>
    <svg style="left:200px" width="90" height="100" viewBox="0 0 90 100"><g transform="rotate(15 45 50)"><rect x="20" y="12" width="50" height="72" rx="4" fill="#fff"/><g stroke="#9b0a0c" stroke-width="4"><line x1="30" y1="30" x2="60" y2="30"/><line x1="30" y1="42" x2="60" y2="42"/><line x1="30" y1="54" x2="60" y2="54"/><line x1="30" y1="66" x2="50" y2="66"/></g></g></svg></div>
  <div class="benefit" style="left:714px"><h4>Budget Control</h4><p>Lorem Ipsum is simply dummy text of the printing and type-setting industry.</p>
    <svg style="left:175px" width="100" height="110" viewBox="0 0 100 110"><g transform="rotate(-40 50 55)"><path d="M35 25h30l8 14v55H27V39z" fill="#fff"/><circle cx="50" cy="38" r="5" fill="#000"/><text x="50" y="80" text-anchor="middle" font-family="Roboto Slab, serif" font-weight="700" font-size="28" fill="#000">$</text></g><path d="M60 20c10-14 26-6 18 8" fill="none" stroke="#fff" stroke-width="4"/></svg></div>
</section>

<footer class="site-footer">
  <div class="footer-col" style="left:101px;width:210px"><h5>ABOUT US</h5><p>Contrary to popular belief, Lorem Ipsum is not simply random text. It has roots in a piece of classical Latin literature from 45 BC, making it over 2000 years old.</p></div>
  <div class="footer-col" style="left:358px"><h5>TERMS &amp; CONDITIONS</h5><ul><li>Shipping &amp; taxes</li><li>Return policy</li><li>Careers</li><li>Affiliates</li><li>Legal Notice</li><li>Privacy &amp; Security</li><li>Sitemap</li></ul></div>
  <div class="footer-col" style="left:598px;width:240px"><h5>CONTACT US</h5><p>Sed ut perspiciatis unde omnis iste natus error sit voluptatem accusantium.</p><p style="margin-top:8px">To order: <span class="hot">+12 345 6789</span></p><p style="margin-top:8px">Client support: <span class="hot">+12 0000000</span></p><p style="margin-top:8px">Email: hello@maplewickhaven.com</p></div>
  <div class="footer-col" style="left:896px;width:200px"><h5>SHIPPING AND RETURN</h5><p>At vero eos et accusamus et iusto odio dignissimos ducimus qui blanditiis praesentium voluptatum deleniti atque corrupti quos dolores et quas.</p></div>
</footer>
<div class="footer-bottom">
  <div class="copyright">© 2015 Maplewick Haven Supply . All rights reserved</div>
  <div class="social"><span></span><span></span><span></span><span></span><span></span><span></span></div>
  <div class="help">Need Help: <b>(010) 888-8888</b></div>
  <nav class="footer-links"><a href="#">Home</a><a href="#">About US</a><a href="#">FAQ</a><a href="#">Blog</a><a href="#">Join Our Newsletter</a><a href="#">Privacy</a></nav>
</div>

</body>
</html>
```